Copper lark buildworks

Copper lark buildworks is a small construction company.
Who is a licenced builder, Carpenter, joiner,
working on heritage ,new build, speacial projects and sometimes furniture

Industry/Entity Type

Construction

```html
<!DOCTYPE html>
<html lang="en">
<head>
<meta charset="utf-8">
<title>Copper lark buildworks – Business Card</title>
<link href="https://fonts.googleapis.com/css2?family=Roboto+Slab:wght@400;500&family=Open+Sans:wght@400;600&display=swap" rel="stylesheet">
<style>
  :root {
    --backdrop: #e9d6b8;
    --card-white: #ffffff;
    --brand-green: #16a50c;
    --brand-green-light: #22b817;
    --ink-dark: #333333;
    --ink-body: #2b2b2b;
    --shadow: rgba(40, 25, 10, 0.35);
  }
  html, body {
    margin: 0;
    padding: 0;
    width: 1200px;
    height: 900px;
    overflow: hidden;
    background: var(--backdrop);
  }
  .canvas {
    position: relative;
    width: 1200px;
    height: 900px;
    background: var(--backdrop);
  }
  .card {
    position: absolute;
    top: 200px;
    width: 310px;
    height: 500px;
    box-shadow: 4px 6px 12px var(--shadow);
  }
  .card-front {
    left: 265px;
    background: var(--card-white);
    border-radius: 44px 0 44px 0;
  }
  .card-back {
    left: 641px;
    background: linear-gradient(160deg, var(--brand-green-light), var(--brand-green) 60%);
    border-radius: 0 44px 0 44px;
  }
  .brand-mark {
    position: absolute;
    left: 0;
    right: 0;
    display: flex;
    align-items: center;
    justify-content: center;
    gap: 8px;
    font-family: "Roboto Slab", serif;
    font-weight: 500;
  }
  .card-front .brand-mark {
    top: 300px;
    color: var(--brand-green);
    font-size: 19px;
  }
  .brand-dot {
    width: 14px;
    height: 14px;
    border-radius: 50%;
    background: currentColor;
    flex: none;
  }
  .company-name {
    position: absolute;
    top: 182px;
    left: 0;
    right: 0;
    text-align: center;
    font-family: "Roboto Slab", serif;
    font-size: 20px;
    color: var(--ink-dark);
    margin: 0;
  }
  .card-front .brand-mark { top: 95px; }
  .contact {
    position: absolute;
    left: 29px;
    top: 292px;
    font-family: "Open Sans", sans-serif;
    color: var(--ink-body);
  }
  .person-name {
    font-family: "Roboto Slab", serif;
    font-size: 20px;
    margin: 0;
    line-height: 1.2;
    color: var(--ink-dark);
  }
  .person-name .first { color: var(--brand-green); }
  .person-role {
    font-size: 13px;
    margin: 2px 0 14px;
  }
  .contact-list {
    list-style: none;
    margin: 0;
    padding: 0;
    font-size: 13px;
    line-height: 18.5px;
  }
  .contact-list li {
    display: flex;
    align-items: center;
    gap: 7px;
  }
  .contact-list svg {
    width: 11px;
    height: 11px;
    fill: var(--brand-green);
    flex: none;
  }
  .address {
    font-size: 13px;
    line-height: 18px;
    margin: 9px 0 0;
  }
  .card-back .brand-mark {
    top: 238px;
    color: var(--card-white);
    font-size: 22px;
  }
</style>
</head>
<body>
<div class="canvas">
  <section class="card card-front">
    <div class="brand-mark"><span class="brand-dot"></span><span>Copper lark buildworks</span></div>
    <h1 class="company-name">Copper lark buildworks</h1>
    <div class="contact">
      <p class="person-name"><span class="first">Harriet</span> Voss</p>
      <p class="person-role">Managing Director</p>
      <ul class="contact-list">
        <li><svg viewBox="0 0 12 12"><path d="M1 4c0-2 2-3 5-3s5 1 5 3H8.5V3h-5v1zM2 5h8l1 6H1z"/></svg>044-310 772 518</li>
        <li><svg viewBox="0 0 12 12"><path d="M3 0h6a1 1 0 0 1 1 1v10a1 1 0 0 1-1 1H3a1 1 0 0 1-1-1V1a1 1 0 0 1 1-1zm0 2v7h6V2z"/></svg>044-310 772 518</li>
        <li><svg viewBox="0 0 12 12"><path d="M0 2h12v1L6 7 0 3zm0 2.5 6 4 6-4V10H0z"/></svg>hello@copperlark.example</li>
        <li><svg viewBox="0 0 12 12"><circle cx="6" cy="6" r="6"/></svg>www.copperlark.example</li>
      </ul>
      <p class="address">48, Tannery Lane Yard<br>Northmoor, 408812.</p>
    </div>
  </section>
  <section class="card card-back">
    <div class="brand-mark"><span class="brand-dot"></span><span>Copper lark buildworks</span></div>
  </section>
</div>
</body>
</html>
```